Mira Ellsworth ADHD coach needs a flyer

I need a flyer to be sent by email. the copy is attached. It can be changed/reduced to fit the flyer. I would like to keep my website colors. My website is www.miraellsworth.net - Thank you!

```html
<!DOCTYPE html>
<html lang="en">
<head>
<meta charset="utf-8">
<title>Mira Ellsworth – ADHD and Academic Coach</title>
<link href="https://fonts.googleapis.com/css2?family=Oswald:wght@300;400&family=Jost:ital,wght@0,400;0,500;0,700;1,400&display=swap" rel="stylesheet">
<style>
:root{
  --stage:#202020;
  --paper:#ffffff;
  --brand:#94b3bf;
  --brand-pale:#dce8ec;
  --brand-soft:#c4d7de;
  --ink:#2b2b2b;
  --ink-soft:#3f4447;
  --slate:#6a6a6a;
}
*{margin:0;padding:0;box-sizing:border-box}
html,body{width:840px;height:1200px;overflow:hidden;background:var(--stage)}
body{position:relative;font-family:"Jost",sans-serif;color:var(--ink)}
.page{position:absolute;left:85px;width:670px;height:518px;background:var(--paper);overflow:hidden}
.page--front{top:65px}
.page--back{top:617px}
.photo{position:absolute}

/* front */
.name-block{position:absolute;left:0;top:0;width:223px;height:120px;background:var(--brand-pale);padding:20px 0 0 28px}
.name-block h1{font-family:"Oswald",sans-serif;font-weight:300;color:var(--brand);font-size:38px;line-height:42px;letter-spacing:.5px;white-space:nowrap}
.credentials{position:absolute;left:0;top:120px;width:223px;height:24px;text-align:center;font-family:"Oswald",sans-serif;font-weight:300;font-size:12px;line-height:24px;color:var(--ink-soft)}
.portrait{left:0;top:144px;width:223px;height:349px;background:linear-gradient(180deg,#b4bcbf,#9aa3a6 60%,#c9b7b8)}
.site-url{position:absolute;top:493px;height:25px;line-height:25px;font-size:9px}
.site-url--left{left:0;width:223px;text-align:center;color:var(--ink-soft)}
.site-url--right{left:223px;width:447px;text-align:right;padding-right:28px;background:var(--brand);color:#fff}
.headline-band{position:absolute;left:223px;top:0;width:447px;height:120px;background:var(--brand);padding:27px 44px 0 24px}
.headline-band h2{font-weight:500;color:#fff;font-size:19px;line-height:24.5px}
.intro{position:absolute;left:248px;top:140px;width:416px;display:flex;gap:34px;font-size:8.4px;line-height:11.2px;color:var(--ink-soft);z-index:1}
.intro .col{width:188px}
.intro p{margin-bottom:11px}
.intro .lead{font-weight:700;color:var(--ink)}
.student-group{left:223px;top:345px;width:447px;height:148px;background:linear-gradient(180deg,rgba(255,255,255,1) 0%,rgba(214,226,200,.8) 22%,#8fa7b3 55%,#7a6a58 100%)}

/* back */
.focus{position:absolute;left:27px;top:24px;width:178px;font-size:7.6px;line-height:9.8px;color:var(--ink-soft)}
.focus h3{font-size:11px;line-height:13px;font-weight:700;color:var(--ink)}
.focus h3 em{display:block;font-weight:400;font-size:11px}
.focus p{margin-top:10px}
.focus ul{margin-top:4px;padding-left:13px}
.focus li{margin-bottom:4px}
.library-pair{left:0;top:300px;width:223px;height:193px;background:linear-gradient(135deg,#dfe4e8,#b8c0c7 50%,#54606a)}
.study-group{left:223px;top:0;width:447px;height:196px;background:linear-gradient(160deg,#eef0f2,#c9c2b6 45%,#56637a)}
.results{position:absolute;left:223px;top:196px;width:223px;height:297px;background:var(--brand)}
.voices{position:absolute;left:446px;top:196px;width:224px;height:222px;background:var(--brand)}
.band{background:var(--brand-soft);color:var(--ink);padding:4px 14px}
.band h3{font-size:11px;line-height:14px;font-weight:700}
.band h3 em{display:block;font-weight:400;font-size:11px}
.results ul,.voices .quotes{padding:8px 14px 6px 27px;font-size:7.6px;line-height:9.8px;color:#fff}
.results li{margin-bottom:4px}
.voices .quotes{padding-left:16px}
.voices p{margin-bottom:7px}
.next-steps{position:absolute;left:446px;top:418px;width:224px;height:75px;background:var(--slate);color:#fff;padding:9px 16px;font-size:8.4px;line-height:10.5px}
.next-steps h3{font-size:11px;line-height:13px;font-weight:700;margin-bottom:2px}
.footer-url{position:absolute;left:0;top:493px;width:670px;height:25px;line-height:25px;text-align:right;padding-right:28px;font-size:9px;color:var(--ink-soft)}
</style>
</head>
<body>

<section class="page page--front">
  <div class="name-block"><h1>MIRA<br>ELLSWORTH</h1></div>
  <div class="credentials">Ph.D.&nbsp; | &nbsp;ADHD and Academic Coach</div>
  <div class="photo portrait" role="img" aria-label="Portrait of the coach, arms crossed, in a pale pink jacket"></div>
  <div class="site-url site-url--left">www.miraellsworth.net</div>

  <div class="headline-band">
    <h2>Helping Your Child with ADHD or Other Learning Challenges Thrive in College and Beyond</h2>
  </div>

  <div class="photo student-group" role="img" aria-label="Row of smiling college students sitting outdoors with laptops and tablets"></div>

  <div class="intro">
    <div class="col">
      <p class="lead">Academic success coaching that leads to lifelong transformation for students with ADHD and similar challenges that may have impeded their ability to thrive.</p>
      <p>Sending your child off to college can feel scary, especially if that college is hundreds of miles away. You worry about how they'll do on their own—whether they'll make friends, earn good grades, and be happy—especially without you there to support them daily. You know your child is bright, and you want them to have a great future, but you're concerned they will struggle without the right support and resources.</p>
      <p>You don't need to feel helpless as you send your child off to this next stage of their lives.</p>
    </div>
    <div class="col">
      <p>Mira is dedicated to making that transition easier for everyone. Mira Ellsworth has years of experience helping students thrive despite their challenges. She sees your child's potential and helps them see it, too. She provides a safety net as they adjust to a new environment at college. Her services are comprehensive and adaptable, based on the requirements of each individual: helping with course selection and scheduling, time management, study strategies, focus, making new friends, and adapting to change. Through it all, Mira guides students through fundamental work on mindset to ensure that changes stick.</p>
    </div>
  </div>

  <div class="site-url site-url--right">www.miraellsworth.net</div>
</section>

<section class="page page--back">
  <div class="focus">
    <h3>EMPOWERING FOCUS:<em>HOW MIRA HELPS</em></h3>
    <p>Mira has taken students from failing to a 3.0 GPA, and from a C student to the Dean's List, in just one semester. It doesn't take years to provide lasting results; all it takes is the right guide.</p>
    <p>Uniquely positioned to help your child, Mira:</p>
    <ul>
      <li>Tailors support so that your child improves focus and maximizes their potential in college and beyond.</li>
      <li>Understands your child's unique needs - she sees the gifts that others often miss.</li>
      <li>Knows the academic landscape intimately, including the challenges faced by students with ADHD and other conditions.</li>
      <li>Helps with the logistics of scheduling in a way that most advisors can't, enrolling students in the courses that best suit their learning style.</li>
      <li>Nurtures the brilliance in your bright child.</li>
      <li>Provides a balance between encouraging students and challenging them.</li>
    </ul>
  </div>
  <div class="photo library-pair" role="img" aria-label="Two students reading together in a library"></div>

  <div class="photo study-group" role="img" aria-label="Four students gathered around a table studying papers"></div>

  <div class="results">
    <div class="band"><h3>REALIZING POTENTIAL:<em>THE TRANSFORMATION YOU'LL SEE IN YOUR CHILD</em></h3></div>
    <ul>
      <li>A mindset of self-belief and increased confidence.</li>
      <li>Higher grades and the drive to graduate.</li>
      <li>Social integration and making friends.</li>
      <li>Happiness and fulfilment.</li>
      <li>A deep sense of personal achievement and pride.</li>
    </ul>
    <div class="band"><h3>You Will Have:</h3></div>
    <ul>
      <li>Less stress, knowing that your child is in good hands.</li>
      <li>Fewer sleepless nights worrying about your child.</li>
      <li>Confidence that they are receiving the right support.</li>
      <li>Joy and pride at seeing them do well.</li>
    </ul>
  </div>

  <div class="voices">
    <div class="band"><h3>What Parents Say</h3></div>
    <div class="quotes">
      <p>“Mira was the glue that kept our daughter in college… as our daughter's Academic Coach, [she] gave our daughter the ability to finish strong by empowering her with the skills needed to be successful.”—<em>Renee</em></p>
      <p>“Mira has always told my daughter not that she <em>can</em> succeed, but that she <em>will</em> succeed.”—<em>Colette</em></p>
    </div>
    <div class="band"><h3>What Students Say</h3></div>
    <div class="quotes">
      <p><em>“Last semester I completed all 16 hours and I had the highest GPA I've ever had!” —Former student</em></p>
      <p>“Under her instruction, my grades began to improve. I ended up making the Dean's List during my time at Brookfield, and I was also inducted into Sigma Tau Rho. I am currently in my first year of law school at Harlow State University, a top tier school.”—<em>Former student</em></p>
    </div>
  </div>

  <div class="next-steps">
    <h3>Next Steps</h3>
    <p>To learn more and discuss your child's individual needs, call <strong>555·013·4827</strong> or email <strong>coach@miraellsworth.net</strong></p>
  </div>

  <div class="footer-url">www.miraellsworth.net</div>
</section>

</body>
</html>
```